Postcard Mail Out - Dwight

We are a real estate company. We need a post card to mail out to potential clients to try and sale their land. We will attached a couple of post cards that we like but we do not want to copy them completely. We do need to put the Equal Housing Opportunity and the Realtor logos with a disclosure saying not intended to solicit currently listed properties. The image below is what we had started working on. We would like to include something about farm land, timber, maybe a pond, something along those lines. The PDF Files attached are a flyer that was mailed out by another company that we do not want to copy completely. Attached also will be our company's Logo.

Requirements
Must have
• We do need to put the Equal Housing Opportunity and the Realtor logos with a disclosure saying not intended to solicit currently listed properties.<br/><br/>At Cobb Harlow Summit Realty, we are blessed to have one of the very best Rural Land Specialists available. Dwight has years of experience promoting and selling rural land properties. Dwight has earned the trust of many landowners, as he is so PASSIONATE in all regards to rural land, farms and ranches. He has made a wide range of landowners very happy throughout his years in Real Estate. Call him today and show him your property, and he will provide you with a free analysis and strategy to maximize the return on your property.
Nice to have
• A picture of Dwight has been added to use on the back of the post card with his phone and number. It would be nice to have a east Texas scenery picture behind him instead of an office.<br/><br/>Please include front and back of post card in your submission.
Should not have
• Should not have Marcus Thorne's information on the postcard. That post card was just to show what we was wanting. The agent we want listed is Dwight Fenwick and his phone number is (555)412-3086.

```html
<!DOCTYPE html>
<html lang="en">
<head>
<meta charset="utf-8">
<title>Land For Sale Postcard – Front and Back</title>
<link rel="stylesheet" href="https://fonts.googleapis.com/css2?family=Open+Sans:wght@400;600;700;800&family=Tinos:wght@400;700&display=swap">
<style>
  :root{
    --stage:#d6d6d6;
    --card:#f2f2f2;
    --ink:#111111;
    --brand-blue:#2a4f8f;
    --brand-blue-dark:#1a3566;
    --brand-blue-light:#4a74b8;
    --mid-gray:#9a9a9a;
    --badge-gray:#8c8c8c;
    --white:#ffffff;
  }
  *{margin:0;padding:0;box-sizing:border-box}
  html,body{width:1200px;height:696px;overflow:hidden;background:var(--stage)}
  .stage{position:relative;width:1200px;height:696px}
  .postcard{position:absolute;top:163px;width:550px;height:370px;background:var(--card);overflow:hidden;box-shadow:0 6px 18px rgba(0,0,0,.25)}
  .postcard--back{left:35px}
  .postcard--front{left:615px}

  /* back */
  .back-scene{position:absolute;inset:0;background:linear-gradient(160deg,#e6e6e6 0%,#c9c9c9 45%,#e2e2e2 75%,#f0f0f0 100%)}
  .back-art{position:absolute;inset:0}
  .compliance{position:absolute;left:14px;top:12px;display:flex;align-items:center;gap:8px}
  .compliance-badge{width:26px;height:26px;background:var(--badge-gray)}
  .disclosure{font-family:'Open Sans',sans-serif;font-size:8px;font-weight:600;color:#444;line-height:1.3;width:150px}
  .stamp-box{position:absolute;left:420px;top:30px;width:92px;height:82px;border:1.5px solid var(--ink)}
  .address-line{position:absolute;height:1px;background:var(--ink)}
  .back-brand{position:absolute;left:40px;top:262px;display:flex;align-items:center;gap:10px}
  .brand-mark{width:22px;height:22px;background:var(--ink)}
  .back-brand .brand-name{font-family:'Tinos',serif;font-weight:400;font-size:19px;line-height:1.05;color:#333}
  .footer-text{position:absolute;left:8px;bottom:6px;color:var(--white);font-family:'Open Sans',sans-serif;font-size:8px;font-weight:600;line-height:1.5}
  .footer-text span{display:inline-flex;align-items:center;gap:4px;margin-right:8px}

  /* front */
  .photo-grid{position:absolute;left:0;top:0;width:100%;height:262px;display:flex;gap:4px;background:var(--white)}
  .photo-tile{flex:1}
  .photo-tile:nth-child(1){background:linear-gradient(180deg,#dedede,#a8a8a8)}
  .photo-tile:nth-child(2){background:linear-gradient(180deg,#d2d2d2,#8f8f8f)}
  .photo-tile:nth-child(3){background:linear-gradient(180deg,#e0e0e0,#9e9e9e)}
  .photo-tile:nth-child(4){background:linear-gradient(180deg,#cfcfcf,#959595)}
  .photo-tile:nth-child(5){background:linear-gradient(180deg,#e4e4e4,#a2a2a2)}
  .grid-wash{position:absolute;left:0;top:0;width:100%;height:262px;background:linear-gradient(180deg,rgba(255,255,255,.55),rgba(255,255,255,.15))}
  .front-brand{position:absolute;right:26px;top:24px;display:flex;align-items:center;gap:10px}
  .front-brand .brand-mark{width:34px;height:34px;background:var(--brand-blue)}
  .front-brand .brand-name{font-family:'Tinos',serif;font-weight:700;font-size:20px;line-height:1.05;color:var(--brand-blue-dark)}
  .tagline{position:absolute;left:0;width:100%;top:112px;text-align:center;font-family:'Tinos',serif;font-weight:700;font-size:24px;letter-spacing:1px;color:var(--brand-blue)}
  .headline{position:absolute;left:0;width:100%;top:136px;text-align:center;font-family:'Open Sans',sans-serif;font-weight:800;font-size:66px;color:var(--ink);letter-spacing:-1px;-webkit-text-stroke:2px var(--white);paint-order:stroke fill}
  .call-us{position:absolute;left:0;width:100%;top:218px;text-align:center;font-family:'Open Sans',sans-serif;font-weight:800;font-size:34px;color:var(--mid-gray);-webkit-text-stroke:1.5px #333;paint-order:stroke fill}
  .rule-black{position:absolute;left:0;top:272px;width:100%;height:7px;background:var(--ink)}
  .phone-band{position:absolute;left:0;top:286px;width:100%;height:60px;background:linear-gradient(90deg,var(--brand-blue-light),var(--brand-blue) 50%,var(--brand-blue-dark));display:flex;align-items:center;justify-content:center}
  .phone-band .phone{font-family:'Open Sans',sans-serif;font-weight:800;font-size:46px;color:var(--white)}
  .base-band{position:absolute;left:0;top:352px;width:100%;height:18px;background:linear-gradient(90deg,var(--brand-blue-light),var(--brand-blue-dark))}
</style>
</head>
<body>
<main class="stage">

  <section class="postcard postcard--back" aria-label="Postcard back">
    <div class="back-scene" role="img" aria-label="Faded photograph of a stone country house with trees"></div>
    <svg class="back-art" width="550" height="370" viewBox="0 0 550 370">
      <defs>
        <linearGradient id="thumbTone" x1="0" y1="0" x2="0" y2="1">
          <stop offset="0" stop-color="#bdbdbd"/><stop offset="1" stop-color="#555"/>
        </linearGradient>
      </defs>
      <polygon points="342,0 356,0 266,370 252,370" fill="#111"/>
      <polygon points="0,330 276,330 266,370 0,370" fill="#111"/>
      <g stroke="#fff" stroke-width="4">
        <circle cx="335" cy="55" r="27" fill="url(#thumbTone)" role="img" aria-label="Photo of a barn on farmland"/>
        <circle cx="318" cy="125" r="27" fill="url(#thumbTone)" role="img" aria-label="Photo of a country road through fields"/>
        <circle cx="301" cy="195" r="27" fill="url(#thumbTone)" role="img" aria-label="Photo of planted crop rows"/>
        <circle cx="284" cy="265" r="27" fill="url(#thumbTone)" role="img" aria-label="Photo of a ranch home"/>
      </g>
    </svg>
    <div class="compliance">
      <div class="compliance-badge" role="img" aria-label="Equal housing opportunity badge"></div>
      <div class="compliance-badge" role="img" aria-label="Realtor membership badge"></div>
      <p class="disclosure">Not intended to solicit properties currently listed for sale.</p>
    </div>
    <div class="stamp-box"></div>
    <div class="address-line" style="left:385px;top:180px;width:140px"></div>
    <div class="address-line" style="left:375px;top:212px;width:150px"></div>
    <div class="address-line" style="left:365px;top:244px;width:160px"></div>
    <div class="address-line" style="left:355px;top:276px;width:170px"></div>
    <div class="back-brand">
      <div class="brand-mark"></div>
      <div class="brand-name">Cobb Harlow<br>Summit Realty</div>
    </div>
    <div class="footer-text">
      <div><span>
        <svg width="8" height="8" viewBox="0 0 10 10"><path d="M2 1l2 2-1 1.5c.8 1.5 1.5 2.2 3 3L7.5 6l2 2-1.5 1.5C4 9 1 6 .5 1.5z" fill="#fff"/></svg>(555)412-3086</span><span>www.summitlandprop.com</span></div>
      <div><span>
        <svg width="8" height="8" viewBox="0 0 10 10"><path d="M5 0a3.5 3.5 0 0 1 3.5 3.5C8.5 6 5 10 5 10S1.5 6 1.5 3.5A3.5 3.5 0 0 1 5 0z" fill="#fff"/><circle cx="5" cy="3.5" r="1.2" fill="#111"/></svg>Pinecrest, TX 75901. 48 W Oak St. Pinecrest, TX 75901.</span></div>
    </div>
  </section>

  <section class="postcard postcard--front" aria-label="Postcard front">
    <div class="photo-grid">
      <div class="photo-tile" role="img" aria-label="Photo of a rural dirt road"></div>
      <div class="photo-tile" role="img" aria-label="Photo of open pasture"></div>
      <div class="photo-tile" role="img" aria-label="Photo of a farmhouse by a field"></div>
      <div class="photo-tile" role="img" aria-label="Photo of timber land"></div>
      <div class="photo-tile" role="img" aria-label="Photo of cleared acreage"></div>
    </div>
    <div class="grid-wash"></div>
    <div class="front-brand">
      <div class="brand-mark"></div>
      <div class="brand-name">Cobb Harlow<br>Summit Realty</div>
    </div>
    <p class="tagline">SPECIALIZING IN RURAL LAND SALES</p>
    <h1 class="headline">Land For Sale?</h1>
    <p class="call-us">CALL US</p>
    <div class="rule-black"></div>
    <div class="phone-band"><span class="phone">(555)412-3086</span></div>
    <div class="base-band"></div>
  </section>

</main>
</body>
</html>
```